Executive Business Card for Healthcare Company [Need Today]

I need a business card design for a healthcare company. The only branding the company has thus far is a logo. The cards will be utilized by company executives. The design I envision will be vibrant and appealing but with a corporate feel. They shouldn't be too casual or playful. I would like to complete this project TODAY if possible.

Target Market(s)

Healthcare vendors, other executives in healthcare and pharmaceuticals

Industry/Entity Type

Pharmaceutical

Contact Information for Business Card

See attachment

Font styles to use
Serif
Sans Serif

Colors

Designer to choose colors to be used in the design.

```html
<!DOCTYPE html>
<html lang="en">
<head>
<meta charset="utf-8">
<title>Corvela Therapeutics – Business Card</title>
<link href="https://fonts.googleapis.com/css2?family=Questrial&family=EB+Garamond:wght@400;500&family=Open+Sans:wght@400&display=swap" rel="stylesheet">
<style>
  :root{
    --backdrop:#8fa8af;
    --card:#ffffff;
    --teal:#3ec3cb;
    --ink:#1e1e1e;
    --grey:#6b6b6b;
    --icon:#222222;
    --sans:'Questrial', sans-serif;
    --serif:'EB Garamond', serif;
    --body:'Open Sans', sans-serif;
  }
  *{margin:0;padding:0;box-sizing:border-box}
  html,body{width:1200px;height:800px;overflow:hidden;background:var(--backdrop)}
  .canvas{position:relative;width:1200px;height:800px}
  .card{position:absolute;left:326px;width:538px;height:307px;background:var(--card);overflow:hidden}
  .card--front{top:24px}
  .card--back{top:426px}

  /* brand name */
  .brand-name{position:absolute;font-family:var(--sans);font-weight:400;color:var(--teal);line-height:1;white-space:nowrap}
  .card--front .brand-name{left:0;right:0;top:98px;text-align:center;font-size:46px}

  .find-us{position:absolute;left:0;right:0;top:210px;text-align:center;font-family:var(--serif);font-size:17px;color:var(--ink)}
  .social{position:absolute;left:226px;top:240px;display:flex;gap:8px}
  .social span{width:18px;height:18px;background:var(--teal);border-radius:2px}

  .web-band{position:absolute;left:0;right:0;top:286px;height:12px;display:flex;align-items:center}
  .web-band .bar{flex:1;height:10px;background:var(--teal)}
  .web-band .url{padding:0 8px;font-family:var(--body);font-size:14px;color:var(--ink)}

  /* back */
  .header-strip{position:absolute;left:7px;top:11px;width:517px;height:81px;background:#fff;box-shadow:0 6px 10px rgba(0,0,0,.18)}
  .header-strip .brand-name{left:18px;top:27px;font-size:26px}
  .company{position:absolute;right:12px;top:23px;font-family:var(--sans);font-size:30px;color:var(--ink);white-space:nowrap}

  .contact{position:absolute;left:33px;display:flex;align-items:center;gap:8px;font-family:var(--body);color:var(--ink)}
  .contact .ico{width:28px;height:28px;border-radius:50%;background:var(--icon);display:flex;align-items:center;justify-content:center;flex:none}
  .contact--email{top:122px;font-size:14px}
  .contact--phone{top:160px;font-size:12px}
  .contact--mobile{top:200px;font-size:19px}
  .contact--address{top:238px;align-items:flex-start;font-family:var(--serif);font-size:16px;line-height:20px}

  .person{position:absolute;right:26px;top:150px;text-align:right}
  .person-name{font-family:var(--serif);font-size:45px;font-weight:500;color:var(--ink);line-height:1.05}
  .person-title{font-family:var(--serif);font-size:22px;font-weight:400;color:var(--ink);margin-top:2px}
  .back-url{position:absolute;left:352px;top:286px;font-family:var(--serif);font-size:12px;color:var(--grey)}
</style>
</head>
<body>
<main class="canvas">

  <section class="card card--front">
    <div class="brand-name">Corvela Therapeutics</div>
    <p class="find-us">Find Us on:</p>
    <div class="social" aria-label="Social media links"><span></span><span></span><span></span><span></span></div>
    <div class="web-band"><span class="bar"></span><span class="url">www.website.com</span><span class="bar"></span></div>
  </section>

  <section class="card card--back">
    <header class="header-strip">
      <div class="brand-name">Corvela</div>
      <div class="company">Corvela Therapeutics</div>
    </header>

    <div class="contact contact--email">
      <span class="ico"><svg width="16" height="12" viewBox="0 0 16 12"><rect x="0.75" y="0.75" width="14.5" height="10.5" fill="none" stroke="#fff" stroke-width="1.5"/><path d="M1 1l7 6 7-6" fill="none" stroke="#fff" stroke-width="1.5"/></svg></span>
      dmarsh@corvelarx.com
    </div>
    <div class="contact contact--phone">
      <span class="ico"><svg width="16" height="14" viewBox="0 0 16 14"><path d="M1 5c0-3 14-3 14 0v1h-4V4H5v2H1z" fill="#fff"/><rect x="3" y="7" width="10" height="6" rx="1" fill="#fff"/></svg></span>
      555-214-0387
    </div>
    <div class="contact contact--mobile">
      <span class="ico"><svg width="14" height="14" viewBox="0 0 14 14"><path d="M3 1l2 3-1.5 1.5c1 2 3 4 5 5L10 9l3 2-1.5 2.5C6 13 1 8 .5 2.5z" fill="#fff"/></svg></span>
      555-618-2740
    </div>
    <div class="contact contact--address">
      <span class="ico"><svg width="12" height="16" viewBox="0 0 12 16"><path d="M6 0a6 6 0 0 1 6 6c0 4-6 10-6 10S0 10 0 6a6 6 0 0 1 6-6z" fill="#fff"/><circle cx="6" cy="6" r="2.2" fill="#222"/></svg></span>
      <span>118 Linden Avenue<br>Fairview GA 30500</span>
    </div>

    <div class="person">
      <h1 class="person-name">Daniel Marsh</h1>
      <p class="person-title">Senior Director of Marketing</p>
    </div>
    <p class="back-url">www.website.com</p>
  </section>

</main>
</body>
</html>
```